Redesign two existing website pages and one new landing page for dental office

I need to redesign two webpages on my dental website, the Home page (http://velbridgedental.com) and the Dental Implant Services page (http://www.velbridgedental.com/dental-implant-services) and also create a landing page for the Dental Implant Services page.

Please use the same color scheme, slogans and subtitles for the redesign pages and create a reserved video spot on each page. The video spots should not be too big but not too small either and positioned in a central key location on each of the pages. The final redesigned pages should communicate leadership, confidence and trust.

The new landing page for the Dental implant Services page must not have any hyperlinks on the page and must entice the viewer to give name and email before downloading a "Free" eBook called "Is a Fuller Smile Worth the Wait?" Any added photo images to this new page must be smiling.
Updates

Project Deadline Extended Reason: I got feedback that my project was not long enough so I'm extending it by 5 days. Added Thursday, April 16, 2015

Target Market(s)

People who are middle-age to seniors.

Industry/Entity Type

Dental

Coding

Coded - Design and coding required

Number of Pages Required

3 page

Requirements
Must have
• Compatible with existing website colors and theme.

```html
<!DOCTYPE html>
<html lang="en">
<head>
<meta charset="utf-8">
<title>Velbridge Dental Care</title>
<link rel="stylesheet" href="https://fonts.googleapis.com/css2?family=Lato:wght@400;700&family=Open+Sans:wght@400;600;700&display=swap">
<style>
:root{
  --teal:#3d5f58;
  --teal-dark:#2c4742;
  --teal-light:#5f8a80;
  --nav-active:#8fb7ac;
  --ink:#222;
  --text:#444;
  --muted:#777;
  --band:#efefef;
  --footer:#3a3b3d;
  --footer-deep:#2e2f31;
  --footer-text:#c9c9c9;
  --footer-muted:#8a8a8a;
  --rule:#ddd;
}
*{margin:0;padding:0;box-sizing:border-box}
html,body{width:679px;height:1200px;overflow:hidden;background:#fff}
body{position:relative;font-family:"Open Sans",Arial,sans-serif;color:var(--text)}
.abs{position:absolute}
.top-rule{left:0;top:0;width:679px;height:2px;background:var(--teal-dark)}

.brand{left:84px;top:18px;display:flex;align-items:center;gap:6px;font-family:"Lato",sans-serif;font-size:21px;color:var(--teal-light)}
.brand-dot{width:10px;height:10px;border-radius:50%;background:var(--teal-light)}
.quick{top:22px;display:flex;align-items:center;gap:6px;font-size:8px;line-height:10px;color:#444}
.quick svg{width:18px;height:18px;fill:var(--teal)}

.nav{left:0;top:62px;width:679px;height:24px;background:linear-gradient(#4f7069,#2f4c46)}
.nav ul{list-style:none;position:absolute;left:84px;top:0;display:flex;height:24px}
.nav li{font-size:7.5px;color:#fff;padding:0 11px;line-height:24px;border-right:1px solid rgba(255,255,255,.15)}
.nav li.active{background:var(--nav-active);color:var(--teal-dark)}
.socials{right:84px;top:67px;display:flex;gap:4px}
.socials span{width:13px;height:13px;border-radius:3px;background:#cfe0db}

.hero{left:0;top:86px;width:679px;height:243px;background:radial-gradient(circle at 15% 60%,#e8f6d8 0,#cfeecf 25%,transparent 50%),linear-gradient(100deg,#9fe0ef 0%,#c9f0e2 40%,#dff3cf 75%,#c6ecf0 100%)}
.hero-title{left:83px;top:72px;font-family:"Lato",sans-serif;font-weight:700;font-size:20.5px;line-height:26px;color:var(--teal-dark)}
.btn-appt{left:83px;top:134px;width:176px;height:29px;background:var(--teal-dark);border-radius:3px;display:flex;align-items:center;gap:9px;padding-left:9px;font-family:"Lato",sans-serif;font-size:11.5px;color:#fff}
.btn-appt i{width:19px;height:19px;border-radius:50%;background:#5a7771;display:flex;align-items:center;justify-content:center}
.hero-photo{left:294px;top:0;width:306px;height:243px;background:linear-gradient(160deg,#b6a48f,#4a3f3a 60%,#e4c9a5)}

.col-title{top:357px;font-size:13.5px;letter-spacing:.3px;color:#333}
.circle-img{width:96px;height:96px;border-radius:50%}
.col-sub{font-size:11px;line-height:16px;color:#444}
.col-text{font-size:6.8px;line-height:10.4px;color:#555}
.btn-more{height:16px;padding:0 7px;background:var(--teal-dark);color:#fff;font-size:6.8px;font-weight:600;line-height:16px;border-radius:2px}
.divider{left:334px;top:346px;width:1px;height:162px;background:var(--rule)}

.services{left:0;top:527px;width:679px;height:259px;background:var(--band)}
.services h2{position:absolute;left:0;width:679px;top:17px;text-align:center;font-family:"Open Sans",sans-serif;font-weight:600;font-size:18px;color:#111}
.services .lead{position:absolute;left:0;width:679px;top:46px;text-align:center;font-size:8.6px;color:#222}
.svc{width:140px;text-align:center}
.svc .disc{width:64px;height:64px;border-radius:50%;background:var(--teal);margin:0 auto;display:flex;align-items:center;justify-content:center}
.svc h3{margin-top:18px;font-size:10.5px;font-weight:700;color:#111}
.svc p{margin-top:10px;font-size:6.8px;line-height:10.4px;color:#222;padding:0 16px}

.family-title{left:84px;top:815px;font-size:15px;line-height:22px;font-weight:600;color:#111}
.family-text{left:84px;top:866px;width:250px;font-size:6.8px;line-height:10.4px;color:#333}
.video{left:372px;top:819px;width:224px;height:129px;background:linear-gradient(100deg,#cfe1df,#f1f2ee 55%,#e6d0c4)}
.play{left:466px;top:865px}

.footer{left:0;top:989px;width:679px;height:176px;background:var(--footer)}
.f-head{top:1010px;font-size:7.5px;font-weight:700;color:#eee}
.f-about{left:84px;top:1037px;width:130px;font-size:6.2px;line-height:11.5px;color:var(--footer-muted)}
.f-posts{left:252px;top:1029px;width:97px;list-style:none}
.f-posts li{height:23.5px;line-height:23.5px;font-size:6.2px;color:var(--footer-text);border-bottom:1px solid #55565a}
.f-list{list-style:none;font-size:5.6px;line-height:12.5px;color:var(--footer-text)}
.bottom{left:0;top:1165px;width:679px;height:35px;background:var(--footer-deep)}
.copy{left:84px;top:1178px;font-size:6.2px;color:var(--footer-muted)}
.bottom-icons{right:84px;top:1178px;display:flex;gap:9px}
.bottom-icons span{width:8px;height:8px;border-radius:50%;background:#5d5e62}
</style>
</head>
<body>
<div class="abs top-rule"></div>

<div class="abs brand"><span class="brand-dot"></span>Velbridge Dental Care</div>

<div class="abs quick" style="left:340px">
  <svg viewBox="0 0 24 24"><rect x="6" y="2" width="12" height="20" rx="2"/><rect x="8" y="5" width="8" height="12" fill="#fff"/></svg>
  <span>Get Dr. Hale's<br>Mobile App</span>
</div>
<div class="abs quick" style="left:428px">
  <svg viewBox="0 0 24 24"><rect x="2" y="4" width="16" height="15" rx="1"/><rect x="4" y="8" width="12" height="9" fill="#fff"/><circle cx="18" cy="18" r="5"/><path d="M18 15v6M15 18h6" stroke="#fff" stroke-width="1.5"/></svg>
  <span>New Patient<br>Online Forms</span>
</div>
<div class="abs quick" style="left:520px">
  <svg viewBox="0 0 24 24"><circle cx="12" cy="12" r="10" fill="none" stroke="#3d5f58" stroke-width="1.6"/><path d="M9 6l2 3-1.5 1.5c.8 1.8 2 3 3.8 3.8L15 13l3 2-1.5 2.5C12 17 7 12 6.5 7.5z"/></svg>
  <span>Call Us Today<br>(555)014-2280</span>
</div>

<nav class="abs nav">
  <ul>
    <li class="active">HOME</li>
    <li>ABOUT US</li>
    <li>DENTAL SERVICES</li>
    <li>BLOG</li>
    <li>TESTIMONIALS</li>
    <li>CONTACT US</li>
  </ul>
</nav>
<div class="abs socials"><span></span><span></span><span></span><span></span></div>

<section class="abs hero">
  <div class="abs hero-photo" role="img" aria-label="Smiling family of father, young son and mother"></div>
  <h1 class="abs hero-title">Life-Changing Family<br>Dental Care In Sugar Land</h1>
  <div class="abs btn-appt">
    <i><svg width="11" height="11" viewBox="0 0 24 24" fill="#fff"><rect x="3" y="5" width="18" height="16" rx="1"/><rect x="5" y="9" width="14" height="10" fill="#5a7771"/><path d="M7 11h2v2H7zM11 11h2v2h-2zM15 11h2v2h-2zM7 15h2v2H7zM11 15h2v2h-2z"/></svg></i>
    Request an Appointment
  </div>
</section>

<h2 class="abs col-title" style="left:83px">DENTAL HYGIENE SERVICES</h2>
<div class="abs circle-img" style="left:83px;top:387px;background:radial-gradient(circle,#f4f6f7,#d5e0e3)" role="img" aria-label="Toothbrush and dental floss"></div>
<div class="abs col-sub" style="left:190px;top:382px">Achieve Better Health<br>With Prevention</div>
<p class="abs col-text" style="left:190px;top:418px;width:136px">Maintain healthy teeth and gums with consistent dental exams and teeth cleanings by one of our professional dental hygienists.</p>
<div class="abs btn-more" style="left:190px;top:471px">READ MORE</div>

<div class="abs divider"></div>

<h2 class="abs col-title" style="left:357px">DENTAL EMERGENCY SERVICES</h2>
<div class="abs circle-img" style="left:356px;top:390px;background:radial-gradient(circle,#f3e2c6,#d9c39d)" role="img" aria-label="Woman holding her cheek with toothache"></div>
<div class="abs col-sub" style="left:463px;top:384px">Stop Pain From Tooth<br>Trauma and Infection</div>
<p class="abs col-text" style="left:463px;top:418px;width:136px">Dental emergencies can and will happen suddenly. Treat all tooth infections and dental trauma (without delay) whenever they occur.</p>
<div class="abs btn-more" style="left:463px;top:471px">READ MORE</div>

<section class="abs services">
  <h2>OUR SERVICES</h2>
  <p class="lead">Lorem ipsum dolor sit amet, consectetur adipiscing elit. Suspendisse feugiat nisi non justo bibendum dapibus.</p>
</section>

<div class="abs svc" style="left:69px;top:605px">
  <div class="disc"><svg width="30" height="30" viewBox="0 0 24 24" fill="#fff"><path d="M6 3c2 0 3 1 6 1s4-1 6-1c3 0 4 3 3 6-1 4-2 5-2 9 0 2-1 4-2 4s-2-3-2-5-1-3-3-3-3 1-3 3-1 5-2 5-2-2-2-4c0-4-1-5-2-9C2 6 3 3 6 3z"/></svg></div>
  <h3>BEAUTIFUL DENTURES</h3>
  <p>Lorem ipsum dolor sit amet, consectetur adipiscing elit. Suspendisse feugiat nisi non justo bibendum dapibus.</p>
</div>
<div class="abs svc" style="left:206px;top:605px">
  <div class="disc"><svg width="38" height="20" viewBox="0 0 38 20" fill="#fff"><path d="M1 5c6-4 12-4 18-1 6-3 12-3 18 1-4 12-14 15-18 15S5 17 1 5z"/><path d="M6 7h26c-3 4-8 5-13 5S9 11 6 7z" fill="#3d5f58"/></svg></div>
  <h3>COSMETIC DENTISTRY</h3>
  <p>Lorem ipsum dolor sit amet, consectetur adipiscing elit. Suspendisse feugiat nisi non justo bibendum dapibus.</p>
</div>
<div class="abs svc" style="left:343px;top:605px">
  <div class="disc"><svg width="22" height="34" viewBox="0 0 22 34" fill="#fff"><path d="M4 0c2 0 4 1 7 1s5-1 7-1c3 0 4 3 3 6-1 3-2 5-3 7H4C3 11 2 9 1 6 0 3 1 0 4 0z"/><rect x="3" y="15" width="16" height="3"/><path d="M5 20h12l-1 3H6zM6 25h10l-1 3H7zM8 30h6l-3 4z"/></svg></div>
  <h3>DENTAL IMPLANT</h3>
  <p>Lorem ipsum dolor sit amet, consectetur adipiscing elit. Suspendisse feugiat nisi non justo bibendum dapibus.</p>
</div>
<div class="abs svc" style="left:470px;top:605px">
  <div class="disc"><svg width="34" height="28" viewBox="0 0 34 28" fill="#fff"><circle cx="22" cy="5" r="4"/><path d="M2 22l8-10 6 4 10-6 4 2-12 9-7-3-6 6z"/><rect x="1" y="24" width="22" height="3"/><path d="M28 2h4v3h-4z"/></svg></div>
  <h3>SEDATION DENTISTRY</h3>
  <p>Lorem ipsum dolor sit amet, consectetur adipiscing elit. Suspendisse feugiat nisi non justo bibendum dapibus.</p>
</div>

<h2 class="abs family-title">Comprehensive Family Dentistry in<br>One Sugar Land Dental Office!</h2>
<p class="abs family-text">Lorem ipsum dolor sit amet, consectetur adipiscing elit. Suspendisse feugiat nisi non justo bibendum dapibus. Suspendisse potenti. Vestibulum hendrerit, eros sed posuere vehicula, ante nulla placerat dolor, quis tristique libero dolor eget diam. Mauris id arcu hendrerit, mollis neque nec, mollis enim. Phasellus consequat nisl sed dolor malesuada ornare. Duis quam erat, hendrerit sed pellentesque vitae, porttitor in erat. Vestibulum convallis a nisl vitae feugiat. Quisque blandit odio felis, at molestie odio lacinia id.</p>
<div class="abs video" role="img" aria-label="Video still of a dentist and a smiling patient giving thumbs up"></div>
<svg class="abs play" width="36" height="36" viewBox="0 0 36 36"><circle cx="18" cy="18" r="16" fill="rgba(255,255,255,.45)" stroke="#fff" stroke-width="2.5"/><path d="M14 10l11 8-11 8z" fill="#fff"/></svg>

<footer class="abs footer"></footer>
<h4 class="abs f-head" style="left:84px">ABOUT US</h4>
<p class="abs f-about">Lorem ipsum ex vix illud nonummy, novum tation et his. At vix scriptaset patrioque scribentur, at pro fugit erts verterem molestiae, sed et vivendo ali Lorem ipsum ex vix illud nonummy, novum tation et his. At vix scripta patrioque scribentur...</p>

<h4 class="abs f-head" style="left:252px">RECENT POSTS</h4>
<ul class="abs f-posts">
  <li>Blog Slideshow Post</li>
  <li>Aenean Odio Mauris</li>
  <li>Blog Image Post</li>
  <li>Blog Video Post</li>
  <li>Donec Suscipit Dim Euismods</li>
</ul>

<h4 class="abs f-head" style="left:396px">NAVIGATION</h4>
<ul class="abs f-list" style="left:396px;top:1030px">
  <li>&nbsp;HOME</li><li>ABOUT US</li><li>DENTAL SERVICES</li><li>BLOG</li><li>TESTIMONIALS</li><li>CONTACT US</li>
</ul>

<h4 class="abs f-head" style="left:510px">STAY IN TOUCH</h4>
<ul class="abs f-list" style="left:510px;top:1030px">
  <li>SOMEWHERE IN OAK MEADOW</li><li>42 ALDER LANE</li><li>&nbsp;(555) 014-2280</li><li>HELLO@VELBRIDGEDENTAL.COM</li>
</ul>

<div class="abs bottom"></div>
<p class="abs copy">©2015 Velbridge Dental Care, Harborline Medical Center</p>
<div class="abs bottom-icons"><span></span><span></span><span></span><span></span><span></span><span></span></div>
</body>
</html>
```